Tidewell-Network Theme For Forums!

We are looking for a theme for our forums. The forums are ran off Invision Power Boards. We have a basic theme on there now but we want more our own feel. If possible have some longboarding accept incorporated in the theme. We want the theme to have some red in it to match our logo. Tidewell-network.com

Target Market(s)

Skatingboarding & Longboarding

Coding

Coded - Design and coding required

Number of Pages Required

1 page

Colors
f04a50

```html
<!DOCTYPE html>
<html lang="en">
<head>
<meta charset="utf-8">
<title>Tidewell-Network Forums</title>
<link href="https://fonts.googleapis.com/css2?family=Open+Sans:wght@400;600;700&display=swap" rel="stylesheet">
<style>
:root{
  --red:#e0001b;
  --dark:#1f1f1f;
  --ink:#222;
  --muted:#777;
  --row:#efefef;
  --head:#dcdcdc;
  --side:#dadada;
  --page:#ffffff;
  --topbar:#f2f2f2;
  --footer:#2e2e2e;
  --ad-top:#0c2a54;
  --ad-bottom:#2a5e98;
}
*{box-sizing:border-box;margin:0;padding:0}
html,body{width:1075px;height:1200px;overflow:hidden}
body{font-family:'Open Sans',sans-serif;color:var(--ink);background:var(--page);position:relative}
.topbar{height:71px;background:var(--topbar);position:relative}
.brand{position:absolute;left:14px;top:22px;display:flex;align-items:center;gap:8px;font-weight:700;font-size:22px;color:var(--red);letter-spacing:.2px}
.brand-dot{width:14px;height:14px;background:var(--red);border-radius:50%}
.search{position:absolute;left:643px;top:24px;width:176px;height:24px;border:1px solid #ccc;background:#fff;font-size:9px;color:#888;padding:6px 8px;display:flex;justify-content:space-between;align-items:center}
.register{position:absolute;left:831px;top:24px;width:59px;height:24px;background:var(--red);color:#fff;font-size:9px;font-weight:600;display:flex;align-items:center;justify-content:center}
.vsep{position:absolute;left:907px;top:8px;width:1px;height:54px;background:#bbb}
.login{position:absolute;left:922px;top:7px}
.login-title{font-size:10px;color:var(--red);display:flex;align-items:center;gap:4px;margin-bottom:4px}
.login input{display:block;width:95px;height:16px;border:1px solid #bbb;font:7px 'Open Sans',sans-serif;padding:0 5px;margin-bottom:5px;background:#fff}
.login-btn{position:absolute;left:100px;top:38px;width:38px;height:16px;background:#2a2a2a;color:#fff;font-size:7px;display:flex;align-items:center;justify-content:center}
.nav{height:38px;background:var(--dark);border-bottom:3px solid var(--red);display:flex;padding-left:14px}
.nav a{font-size:12px;color:#ddd;text-decoration:none;padding:0 19.5px;display:flex;align-items:center}
.nav a.active{background:var(--red);color:#fff;padding:0 22px}
.sidebar-bg{position:absolute;left:781px;top:110px;width:294px;height:990px;background:var(--side)}
.main{position:absolute;left:14px;top:134px;width:746px}
.board{margin-bottom:15px}
.board-head{height:32px;background:var(--red);color:#fff;font-size:13px;font-weight:600;display:flex;align-items:center;justify-content:space-between;padding:0 14px}
.toggle{width:12px;height:12px;background:#fff;border-radius:2px;position:relative}
.toggle::after{content:"";position:absolute;left:3px;right:3px;top:5px;height:2px;background:var(--red)}
.grid{display:grid;grid-template-columns:35px 322px 115px 100px 174px}
.grid>div{border-right:1px solid #fff}
.grid>div:last-child{border-right:0}
.cols{height:31px;background:var(--head);font-size:12px;border-bottom:2px solid #fff}
.cols>div{padding:0 7px;display:flex;align-items:center}
.row{height:47px;background:var(--row);border-bottom:2px solid #fff;font-size:9px}
.row:last-child{border-bottom:0}
.row>div{padding:9px 7px 0}
.row .ico{display:flex;justify-content:center;padding-top:11px}
.sub{font-size:7.5px;color:var(--muted);margin-top:2px}
.last{display:flex;align-items:center;gap:3px}
.pager{display:flex;gap:6px;margin-top:-5px}
.pager span{height:22px;min-width:23px;padding:0 5px;background:#e3e3e3;font-size:9px;color:#444;display:flex;align-items:center;justify-content:center}
.pager .cur{background:#555;color:#fff}
.pager .gap{margin-left:46px}
.sidebar{position:absolute;left:796px;top:134px;width:265px}
.widget{margin-bottom:17px}
.widget-head{height:32px;background:var(--red);color:#fff;font-size:11px;font-weight:600;display:flex;align-items:center;padding:0 12px}
.widget-item{height:43px;background:var(--row);border-bottom:1px solid #d6d6d6;padding:10px 12px 0;font-size:9.5px}
.widget-item .sub{font-size:6.5px;margin-top:3px}
.ad{width:265px;height:219px;border:2px solid #333;background:linear-gradient(180deg,var(--ad-top),var(--ad-bottom))}
.footer{position:absolute;left:0;top:1124px;width:1075px;height:76px;background:var(--footer);color:#ddd;text-align:center;font-size:9.5px}
.footer-links{margin-top:22px;word-spacing:2px}
.footer-links span{margin:0 7px;color:#aaa}
.copy{margin-top:9px}
</style>
</head>
<body>
<header class="topbar">
  <div class="brand"><span class="brand-dot"></span>Tidewell-Network</div>
  <div class="search">Search
    <svg width="9" height="9" viewBox="0 0 10 10"><circle cx="4" cy="4" r="3" fill="none" stroke="#666" stroke-width="1.4"/><line x1="6.3" y1="6.3" x2="9" y2="9" stroke="#666" stroke-width="1.4"/></svg>
  </div>
  <div class="register">REGSITER</div>
  <div class="vsep"></div>
  <div class="login">
    <div class="login-title"><svg width="10" height="9" viewBox="0 0 10 9"><path d="M0 3h4V1l3 3.5L4 8V6H0z" fill="#e0001b"/><path d="M6 0h4v9H6V8h3V1H6z" fill="#e0001b"/></svg>Member Login</div>
    <input value="Username" aria-label="Username">
    <input value="Password" aria-label="Password">
    <div class="login-btn">LOGIN</div>
  </div>
</header>
<nav class="nav">
  <a class="active">Forums</a><a>Members</a><a>Calendar</a><a>Blogs</a><a>Gallery</a><a>Shop</a><a>Help</a>
</nav>
<div class="sidebar-bg"></div>

<svg width="0" height="0" style="position:absolute">
  <defs>
    <symbol id="i-doc" viewBox="0 0 12 14"><path d="M0 0h8l4 4v10H0z" fill="#666"/><path d="M8 0v4h4" fill="#999"/><rect x="2" y="7" width="8" height="1" fill="#eee"/><rect x="2" y="9.5" width="8" height="1" fill="#eee"/></symbol>
    <symbol id="i-vid" viewBox="0 0 14 10"><rect x="0" y="1" width="9" height="8" rx="1" fill="#666"/><path d="M9 4l5-3v8L9 6z" fill="#666"/></symbol>
    <symbol id="i-img" viewBox="0 0 14 12"><rect x="2" y="0" width="12" height="9" fill="none" stroke="#666" stroke-width="1.3"/><rect x="0" y="3" width="11" height="9" fill="#666"/><path d="M1.5 11l3-4 2 2 1.5-1.5 2 3.5z" fill="#eee"/></symbol>
    <symbol id="i-clock" viewBox="0 0 10 10"><circle cx="5" cy="5" r="4.2" fill="none" stroke="#444" stroke-width="1.4"/><path d="M4 3l2 2-2 2" fill="none" stroke="#444" stroke-width="1.3"/></symbol>
  </defs>
</svg>

<main class="main">
  <section class="board">
    <div class="board-head">FORUM TOPICS<span class="toggle"></span></div>
    <div class="grid cols"><div></div><div>Topic</div><div>Started By</div><div>Status</div><div>Last Post Info</div></div>
    <div class="grid row"><div class="ico"><svg width="12" height="14"><use href="#i-doc"/></svg></div><div>Praesent iaculis faucibus urna sit amet lacinia<div class="sub">Maecenas consequat justo enim</div></div><div>rkdavies54</div><div>25 Replies<div class="sub">7,548 Views</div></div><div><div class="last"><svg width="8" height="8"><use href="#i-clock"/></svg>Today 2:10 PM</div><div class="sub">By : Milo</div></div></div>
    <div class="grid row"><div class="ico"><svg width="12" height="14"><use href="#i-doc"/></svg></div><div>Maecenas vel tortor accumsan quam varius imperdiet<div class="sub">Maecenas consequat justo enim</div></div><div>rkdavies54</div><div>25 Replies<div class="sub">7,548 Views</div></div><div><div class="last"><svg width="8" height="8"><use href="#i-clock"/></svg>Today 2:10 PM</div><div class="sub">By : Milo</div></div></div>
    <div class="grid row"><div class="ico"><svg width="14" height="10"><use href="#i-vid"/></svg></div><div>Aenean facilisis tincidunt lectus, id dictum nisi luctus eget<div class="sub">Maecenas consequat justo enim</div></div><div>rkdavies54</div><div>25 Replies<div class="sub">7,548 Views</div></div><div><div class="last"><svg width="8" height="8"><use href="#i-clock"/></svg>Today 2:10 PM</div><div class="sub">By : Milo</div></div></div>
    <div class="grid row"><div class="ico"><svg width="14" height="10"><use href="#i-vid"/></svg></div><div>Etiam mattis augue vehicula odio posuere, sit amet tempus<div class="sub">Maecenas consequat justo enim</div></div><div>rkdavies54</div><div>25 Replies<div class="sub">7,548 Views</div></div><div><div class="last"><svg width="8" height="8"><use href="#i-clock"/></svg>Today 2:10 PM</div><div class="sub">By : Milo</div></div></div>
    <div class="grid row"><div class="ico"><svg width="14" height="12"><use href="#i-img"/></svg></div><div>Etiam vel massa elementum, bibendum tellus venenatis, feugiat<div class="sub">Maecenas consequat justo enim</div></div><div>rkdavies54</div><div>25 Replies<div class="sub">7,548 Views</div></div><div><div class="last"><svg width="8" height="8"><use href="#i-clock"/></svg>Today 2:10 PM</div><div class="sub">By : Milo</div></div></div>
  </section>

  <section class="board">
    <div class="board-head">BEST BOARDS<span class="toggle"></span></div>
    <div class="grid cols"><div></div><div>Topic</div><div>Started By</div><div>Status</div><div>Last Post Info</div></div>
    <div class="grid row"><div class="ico"><svg width="12" height="14"><use href="#i-doc"/></svg></div><div>Curabitur venenatis lacinia ornare<div class="sub">Maecenas consequat justo enim</div></div><div>rkdavies54</div><div>25 Replies<div class="sub">7,548 Views</div></div><div><div class="last"><svg width="8" height="8"><use href="#i-clock"/></svg>Today 2:10 PM</div><div class="sub">By : Milo</div></div></div>
    <div class="grid row"><div class="ico"><svg width="12" height="14"><use href="#i-doc"/></svg></div><div>Aliquam erat volutpat. Quisque aliquet ex nec est vestibulum pulvinar<div class="sub">Maecenas consequat justo enim</div></div><div>rkdavies54</div><div>25 Replies<div class="sub">7,548 Views</div></div><div><div class="last"><svg width="8" height="8"><use href="#i-clock"/></svg>Today 2:10 PM</div><div class="sub">By : Milo</div></div></div>
    <div class="grid row"><div class="ico"><svg width="14" height="10"><use href="#i-vid"/></svg></div><div>Pellentesque convallis molestie enim sit amet efficitur<div class="sub">Maecenas consequat justo enim</div></div><div>rkdavies54</div><div>25 Replies<div class="sub">7,548 Views</div></div><div><div class="last"><svg width="8" height="8"><use href="#i-clock"/></svg>Today 2:10 PM</div><div class="sub">By : Milo</div></div></div>
    <div class="grid row"><div class="ico"><svg width="14" height="10"><use href="#i-vid"/></svg></div><div>Etiam id imperdiet lectus<div class="sub">Maecenas consequat justo enim</div></div><div>rkdavies54</div><div>25 Replies<div class="sub">7,548 Views</div></div><div><div class="last"><svg width="8" height="8"><use href="#i-clock"/></svg>Today 2:10 PM</div><div class="sub">By : Milo</div></div></div>
    <div class="grid row"><div class="ico"><svg width="14" height="12"><use href="#i-img"/></svg></div><div>Vivamus lacus justo, ultrices nec erat in, euismod iaculis mauris<div class="sub">Maecenas consequat justo enim</div></div><div>rkdavies54</div><div>25 Replies<div class="sub">7,548 Views</div></div><div><div class="last"><svg width="8" height="8"><use href="#i-clock"/></svg>Today 2:10 PM</div><div class="sub">By : Milo</div></div></div>
  </section>

  <section class="board">
    <div class="board-head">TOP EVENTS<span class="toggle"></span></div>
    <div class="grid cols"><div></div><div>Topic</div><div>Started By</div><div>Status</div><div>Last Post Info</div></div>
    <div class="grid row"><div class="ico"><svg width="12" height="14"><use href="#i-doc"/></svg></div><div>Vivamus eleifend vitae nulla vel malesuada<div class="sub">Maecenas consequat justo enim</div></div><div>rkdavies54</div><div>25 Replies<div class="sub">7,548 Views</div></div><div><div class="last"><svg width="8" height="8"><use href="#i-clock"/></svg>Today 2:10 PM</div><div class="sub">By : Milo</div></div></div>
    <div class="grid row"><div class="ico"><svg width="12" height="14"><use href="#i-doc"/></svg></div><div>Fusce vitae lectus sit amet mi pulvinar maximus<div class="sub">Maecenas consequat justo enim</div></div><div>rkdavies54</div><div>25 Replies<div class="sub">7,548 Views</div></div><div><div class="last"><svg width="8" height="8"><use href="#i-clock"/></svg>Today 2:10 PM</div><div class="sub">By : Milo</div></div></div>
    <div class="grid row"><div class="ico"><svg width="14" height="10"><use href="#i-vid"/></svg></div><div>Aenean placerat, nibh vel accumsan aliquet, magna nibh accumsan<div class="sub">Maecenas consequat justo enim</div></div><div>rkdavies54</div><div>25 Replies<div class="sub">7,548 Views</div></div><div><div class="last"><svg width="8" height="8"><use href="#i-clock"/></svg>Today 2:10 PM</div><div class="sub">By : Milo</div></div></div>
    <div class="grid row"><div class="ico"><svg width="14" height="10"><use href="#i-vid"/></svg></div><div>Cras augue magna, placerat eget nulla non, congue suscipit<div class="sub">Maecenas consequat justo enim</div></div><div>rkdavies54</div><div>25 Replies<div class="sub">7,548 Views</div></div><div><div class="last"><svg width="8" height="8"><use href="#i-clock"/></svg>Today 2:10 PM</div><div class="sub">By : Milo</div></div></div>
    <div class="grid row"><div class="ico"><svg width="14" height="12"><use href="#i-img"/></svg></div><div>Phasellus nisl est, condimentum vitae faucibus in, sollicitudin vel<div class="sub">Maecenas consequat justo enim</div></div><div>rkdavies54</div><div>25 Replies<div class="sub">7,548 Views</div></div><div><div class="last"><svg width="8" height="8"><use href="#i-clock"/></svg>Today 2:10 PM</div><div class="sub">By : Milo</div></div></div>
  </section>

  <div class="pager">
    <span>First</span><span class="cur">1</span><span>2</span><span>3</span><span>4</span><span>5</span><span>6</span><span>7</span>
    <span class="gap">581</span>
    <span><svg width="7" height="8" viewBox="0 0 7 8"><path d="M5 0.5L1.5 4 5 7.5" fill="none" stroke="#444" stroke-width="1.4"/></svg></span>
    <span><svg width="7" height="8" viewBox="0 0 7 8"><path d="M2 0.5L5.5 4 2 7.5" fill="none" stroke="#444" stroke-width="1.4"/></svg></span>
    <span>Last</span>
  </div>
</main>

<aside class="sidebar">
  <section class="widget">
    <div class="widget-head">POPULAR TOPICS</div>
    <div class="widget-item">Nullam lorem urna, tempu<div class="sub">Post by Rhea - 1 June, 2018 - 5:53 PM</div></div>
    <div class="widget-item">Suspendisse gravida ornare erat<div class="sub">Post by Rhea - 1 June, 2018 - 5:53 PM</div></div>
    <div class="widget-item">Vestibulum luctus ex in egestas fringilla<div class="sub">Post by Rhea - 1 June, 2018 - 5:53 PM</div></div>
    <div class="widget-item">Fusce nec leo ac urna pulvinar auctor<div class="sub">Post by Rhea - 1 June, 2018 - 5:53 PM</div></div>
  </section>
  <section class="widget">
    <div class="widget-head">OLD TOPICS</div>
    <div class="widget-item">Mauris bibendum fringilla velit<div class="sub">Post by Rhea - 1 June, 2018 - 5:53 PM</div></div>
    <div class="widget-item">Nulla in lorem at massa pellentesque posuere<div class="sub">Post by Rhea - 1 June, 2018 - 5:53 PM</div></div>
    <div class="widget-item">Nulla tristique posuere molestie<div class="sub">Post by Rhea - 1 June, 2018 - 5:53 PM</div></div>
    <div class="widget-item">Duis ornare erat eget magna dapibus<div class="sub">Post by Rhea - 1 June, 2018 - 5:53 PM</div></div>
  </section>
  <section class="widget">
    <div class="widget-head">MOST COMMENTED TOPICS</div>
    <div class="widget-item">Nam tempus, quam in bibendum<div class="sub">Post by Rhea - 1 June, 2018 - 5:53 PM</div></div>
    <div class="widget-item">Pellentesque blandit lacus eget nunc faucibus<div class="sub">Post by Rhea - 1 June, 2018 - 5:53 PM</div></div>
    <div class="widget-item">Phasellus consequat sagittis nisi suscipit feugiat<div class="sub">Post by Rhea - 1 June, 2018 - 5:53 PM</div></div>
    <div class="widget-item">Cras eget leo sed nunc hendrerit ultricies eu at nis<div class="sub">Post by Rhea - 1 June, 2018 - 5:53 PM</div></div>
  </section>
  <div class="ad" role="img" aria-label="Advertising banner space for a sponsor"></div>
</aside>

<footer class="footer">
  <div class="footer-links">Forums<span>|</span>Members<span>|</span>Calendar<span>|</span>Blogs<span>|</span>Gallery<span>|</span>Shop<span>|</span>Help</div>
  <div class="copy">Copyright &copy; 2018 Tidewell-Network. All rights reserved.</div>
</footer>
</body>
</html>
```